Website for new slot-booking/reservations website/software

For a new software product we need a brand new logo and website for a reservations/booking system. The website should ideally present the main features with information text, contact info, news page as well as registration and pricing pages. As currently primary field of operation the software should be used for tennis but later on, also for other sport types. Also we'd like to be the logo a text-brand which includes the name "zeitfeldo.com" or just "zeitfeldo". The logo should ideally include an icon-design in some way. Generally we are open for ideas.

Bootstrap 4 template is a minimum requirement. (Multi-Page preferred, Single-Page still OK.)

You can use the attached image as an inspiration, but change of colors or other design elements are up to you. Currently the application has a primary color of #5500ff. The website created by you will not include the application itself, so it can have different (but ideally similar) Look&Feel.
Updates

Target Market(s)

Sports, Club-Management

Logo Text

zeitfeldo.com

Coding

Coded - Design and coding required

Number of Pages Required

5+ page

Font styles to use
Sans Serif

Requirements
Must have
• Bootstrap 4 Template, SCSS
Nice to have
• Rapid Loading Times, not too much external JS Libraries.
Should not have
• Extensive animations

```html
<!DOCTYPE html>
<html lang="en">
<head>
<meta charset="utf-8">
<title>Zeitfeldo – Court Booking</title>
<link rel="stylesheet" href="https://fonts.googleapis.com/css2?family=PT+Sans:wght@400;700&family=Poppins:wght@500;600;700&family=Lato:wght@400;700&family=Roboto:wght@400;500;700&display=swap">
<style>
:root{
  --purple:#5500ff;
  --green:#35b27d;
  --ink:#222222;
  --muted:#666666;
  --footer:#000000;
  --white:#ffffff;
}
*{margin:0;padding:0;box-sizing:border-box}
html,body{width:1200px;height:3569px;overflow:hidden;background:var(--white)}
body{position:relative;font-family:"Lato",sans-serif;color:var(--ink)}
.abs{position:absolute}
.center{text-align:center}

/* header */
.topline{left:0;top:0;width:1200px;height:3px;background:var(--green)}
.brand{left:104px;top:36px;display:flex;align-items:center;gap:10px;font-family:"Poppins",sans-serif;font-weight:700;font-size:21px;color:var(--purple)}
.brand-dot{width:26px;height:26px;border-radius:50%;background:var(--purple)}
.nav{top:38px;font-family:"Poppins",sans-serif;font-weight:600;font-size:14px;color:var(--ink)}
.nav.active{color:var(--green)}
.nav.active::after{content:"";display:block;height:2px;background:var(--green);margin-top:7px}
.btn-register{left:933px;top:26px;width:155px;height:45px;border-radius:23px;background:var(--purple);color:var(--white);font-family:"Poppins",sans-serif;font-weight:600;font-size:14px;display:flex;align-items:center;justify-content:center}

/* hero */
.hero{left:0;top:98px;width:1200px;height:564px;background:linear-gradient(180deg,#6c7a4e 0%,#8a8f70 35%,#6e6a55 60%,#a0573a 82%,#b9806a 100%)}
.hero-box{left:147px;top:260px;width:488px;height:233px;background:rgba(40,40,40,.55)}
.hero-title{left:177px;top:272px;font-family:"PT Sans",sans-serif;font-weight:700;font-size:68px;color:var(--white);line-height:1}
.hero-text{left:180px;top:357px;width:420px;font-size:13px;line-height:22px;color:var(--white)}
.btn-green{background:var(--green);color:var(--white);font-family:"Poppins",sans-serif;font-weight:600;font-size:13px;display:flex;align-items:center;justify-content:center;border-radius:23px}
.arrow-btn{width:62px;height:62px;border-radius:50%;background:rgba(255,255,255,.85);display:flex;align-items:center;justify-content:center}

/* sections */
.section-title{left:0;width:1200px;text-align:center;font-family:"PT Sans",sans-serif;font-weight:700;font-size:39px;color:var(--ink)}
.rule{height:3px;width:55px;background:var(--green)}
.section-desc{left:180px;width:840px;text-align:center;font-size:12.5px;line-height:23px;color:var(--muted)}

.feature-circle{width:208px;height:208px;border-radius:50%}
.feature{width:230px;text-align:center}
.feature h3{font-family:"PT Sans",sans-serif;font-weight:700;font-size:24px;color:var(--ink);margin-bottom:10px}
.feature p{font-size:14px;line-height:22px;color:#777}
.round-arrow{width:17px;height:17px;margin:12px auto 0;border-radius:50%;background:var(--green);display:flex;align-items:center;justify-content:center}

.about-title{left:111px;top:1370px;font-family:"PT Sans",sans-serif;font-weight:700;font-size:39px}
.about-text{left:111px;width:465px;font-size:12.5px;line-height:22.3px;color:#555}
.about-photo{left:590px;top:1344px;width:610px;height:494px;background:linear-gradient(160deg,#d9d6cc 0%,#9a968a 40%,#4b4a44 70%,#2c2b28 100%);clip-path:polygon(52px 0,610px 0,610px 494px,0 494px)}

.blog-img{width:298px;height:197px;border-radius:6px;box-shadow:0 2px 8px rgba(0,0,0,.2)}
.blog{width:298px;text-align:center}
.blog h4{font-family:"PT Sans",sans-serif;font-weight:700;font-size:20px;line-height:23px;color:var(--ink);padding:0 50px}
.blog .date{font-family:"Roboto",sans-serif;font-size:15px;color:var(--green);margin-top:15px}
.blog p{font-family:"Roboto",sans-serif;font-size:14px;line-height:26px;color:#777;margin-top:6px}
.blog .more{display:inline-block;margin-top:14px;font-family:"Roboto",sans-serif;font-size:14px;color:var(--green);text-decoration:underline}
.btn-purple{left:504px;top:2501px;width:190px;height:47px;border-radius:24px;background:var(--purple);color:var(--white);font-family:"Roboto",sans-serif;font-weight:500;font-size:15px;display:flex;align-items:center;justify-content:center}

/* contact */
.contact{left:0;top:2644px;width:1200px;height:547px;background:var(--purple)}
.contact-title{left:0;top:2726px;width:1200px;text-align:center;font-family:"Poppins",sans-serif;font-weight:600;font-size:33px;color:var(--white)}
.field{height:56px;background:var(--white);font-family:"Roboto",sans-serif;font-size:14px;color:#666;padding-left:24px;display:flex;align-items:center}
.btn-submit{left:515px;top:3044px;width:170px;height:56px;background:var(--green);color:var(--white);font-family:"Roboto",sans-serif;font-weight:700;font-size:14px;display:flex;align-items:center;justify-content:center}

/* footer */
.footer{left:0;top:3191px;width:1200px;height:378px;background:var(--footer)}
.news-label{left:229px;top:3298px;font-family:"Roboto",sans-serif;font-weight:700;font-size:21px;color:var(--white)}
.news-input{left:499px;top:3288px;width:332px;height:48px;border:2px solid var(--white);border-radius:24px;color:var(--white);font-family:"Roboto",sans-serif;font-size:15px;padding-left:28px;display:flex;align-items:center}
.btn-sub{left:842px;top:3288px;width:129px;height:48px;border-radius:24px;background:var(--green);color:var(--white);font-family:"Roboto",sans-serif;font-weight:700;font-size:14px;display:flex;align-items:center;justify-content:center}
.footer-nav{left:0;top:3371px;width:1200px;display:flex;justify-content:center;gap:18px;font-family:"Roboto",sans-serif;font-weight:700;font-size:14px;color:var(--white)}
.social{top:3421px;width:40px;height:40px;border:1.5px solid var(--white);border-radius:50%}
.footer-rule{left:111px;top:3491px;width:978px;height:1px;background:#333}
.copyright{left:0;top:3514px;width:1200px;text-align:center;font-family:"Lato",sans-serif;font-size:14px;color:var(--white)}
</style>
</head>
<body>

<header>
  <div class="abs topline"></div>
  <div class="abs brand"><span class="brand-dot"></span>ZEITFELDO</div>
  <nav>
    <div class="abs nav active" style="left:400px">Home</div>
    <div class="abs nav" style="left:473px">About us</div>
    <div class="abs nav" style="left:565px">Features</div>
    <div class="abs nav" style="left:657px">Blog</div>
    <div class="abs nav" style="left:719px">Pricing</div>
    <div class="abs nav" style="left:798px">Contact us</div>
  </nav>
  <div class="abs btn-register">Register now</div>
</header>

<section>
  <div class="abs hero" role="img" aria-label="Photo of a tennis player swinging a racket on a clay court"></div>
  <div class="abs hero-box"></div>
  <h1 class="abs hero-title">Zeitfeldo</h1>
  <p class="abs hero-text">Lorem ipsum dolor sit amet, consectetur adipiscing elit, sed do eiusmo d tempor incididunt ut labore et dolore magna</p>
  <div class="abs btn-green" style="left:177px;top:416px;width:157px;height:44px">LEARN MORE</div>
  <div class="abs arrow-btn" style="left:42px;top:336px">
    <svg width="20" height="20" viewBox="0 0 20 20"><path d="M17 10H4M10 4L4 10l6 6" stroke="#35b27d" stroke-width="3" fill="none"/></svg>
  </div>
  <div class="abs arrow-btn" style="left:1097px;top:336px">
    <svg width="20" height="20" viewBox="0 0 20 20"><path d="M3 10h13M10 4l6 6-6 6" stroke="#35b27d" stroke-width="3" fill="none"/></svg>
  </div>
</section>

<section>
  <h2 class="abs section-title" style="top:746px">Our Features</h2>
  <div class="abs rule" style="left:572px;top:805px"></div>
  <p class="abs section-desc" style="top:820px">Lorem ipsum dolor sit amet, consectetur adipiscing elit, sed do eiusmod tempor incididunt ut labore et dolore magna aliqua. Ut enim ad minim veniam, quis nostrud exercitation ullamco</p>

  <div class="abs feature-circle" style="left:130px;top:885px;background:var(--purple)" role="img" aria-label="Icon of a hand holding a rising chart"></div>
  <div class="abs feature-circle" style="left:374px;top:919px;background:var(--green)" role="img" aria-label="Icon of a gear with a wrench"></div>
  <div class="abs feature-circle" style="left:618px;top:885px;background:var(--purple)" role="img" aria-label="Icon of a support agent at a laptop"></div>
  <div class="abs feature-circle" style="left:862px;top:919px;background:var(--green)" role="img" aria-label="Icon of 24 hour service"></div>

  <div class="abs feature" style="left:119px;top:1104px"><h3>Incididun labore</h3><p>Lorem ipsum dolor sit amet, cons ectetur adipiscing elit, sed do eiusmod tempor incidi</p><div class="round-arrow"><svg width="9" height="9" viewBox="0 0 10 10"><path d="M1 5h7M5 2l3 3-3 3" stroke="#fff" stroke-width="2" fill="none"/></svg></div></div>
  <div class="abs feature" style="left:363px;top:1138px"><h3>Incididun labore</h3><p>Lorem ipsum dolor sit amet, cons ectetur adipiscing elit, sed do eiusmod tempor incidi</p><div class="round-arrow"><svg width="9" height="9" viewBox="0 0 10 10"><path d="M1 5h7M5 2l3 3-3 3" stroke="#fff" stroke-width="2" fill="none"/></svg></div></div>
  <div class="abs feature" style="left:607px;top:1104px"><h3>Incididun labore</h3><p>Lorem ipsum dolor sit amet, cons ectetur adipiscing elit, sed do eiusmod tempor incidi</p><div class="round-arrow"><svg width="9" height="9" viewBox="0 0 10 10"><path d="M1 5h7M5 2l3 3-3 3" stroke="#fff" stroke-width="2" fill="none"/></svg></div></div>
  <div class="abs feature" style="left:851px;top:1138px"><h3>Incididun labore</h3><p>Lorem ipsum dolor sit amet, cons ectetur adipiscing elit, sed do eiusmod tempor incidi</p><div class="round-arrow"><svg width="9" height="9" viewBox="0 0 10 10"><path d="M1 5h7M5 2l3 3-3 3" stroke="#fff" stroke-width="2" fill="none"/></svg></div></div>
</section>

<section>
  <h2 class="abs about-title">About us</h2>
  <div class="abs rule" style="left:111px;top:1428px"></div>
  <p class="abs about-text" style="top:1453px">Lorem ipsum dolor sit amet, consectetur adipiscing elit, sed do eiusmod tempor incididunt ut labore et dolore magna aliqua. Ut enim ad minim veniam, quis nostrud exercitation ullamco laboris nisi ut aliquip ex ea commodo conse quat. Duis aute irure dolor in reprehenderit in voluptate velit esse cillum dolo re eu fugiat nulla pariatur. Excepteur sint occaecat cupidatat non proident, sunt in culpa qui officia deserunt mollit anim id est laborum.</p>
  <p class="abs about-text" style="top:1609px">Lorem ipsum dolor sit amet, consectetur adipiscing elit, sed do eiusmod tempor incididunt ut labore et dolore magna aliqua. Ut enim ad minim veniam, quis nostrud exercitation ullamco laboris nisi ut aliquip ex ea commodo conse quat. Duis aute irure dolor in reprehenderit in voluptate velit esse cillum dolo re eu fugiat nulla pariatur. Excepteur sint occaecat cupidatat non proident, sunt in culpa qui officia deserunt mollit anim id est laborum.</p>
  <div class="abs btn-green" style="left:111px;top:1771px;width:155px;height:44px">LEARN MORE</div>
  <div class="abs about-photo" role="img" aria-label="Photo of a tennis racket and ball lying on a court by the net"></div>
</section>

<section>
  <h2 class="abs section-title" style="top:1917px">Latest Blog</h2>
  <div class="abs rule" style="left:572px;top:1975px"></div>
  <p class="abs section-desc" style="top:1995px">Lorem ipsum dolor sit amet, consectetur adipiscing elit, sed do eiusmod tempor incididunt ut labore et dolore magna aliqua. Ut enim ad minim veniam, quis nostrud exercitation ullamco</p>

  <div class="abs blog-img" style="left:112px;top:2076px;background:linear-gradient(180deg,#3d3a2c 0%,#5f4a30 35%,#a0583c 65%,#8e4a32 100%)" role="img" aria-label="Photo of an empty clay tennis court in a stadium"></div>
  <div class="abs blog-img" style="left:452px;top:2076px;background:linear-gradient(180deg,#9fb07a 0%,#7fa4a8 35%,#4f8fc0 65%,#3a7cb5 100%)" role="img" aria-label="Photo of two tennis players standing on a blue court"></div>
  <div class="abs blog-img" style="left:790px;top:2076px;background:linear-gradient(180deg,#5e8f7a 0%,#4b9bc7 45%,#2f86c4 75%,#3f7fb0 100%)" role="img" aria-label="Photo of tennis players giving a high five"></div>

  <article class="abs blog" style="left:112px;top:2299px"><h4>Lorem ipsum dolor sit amet</h4><div class="date">Jun 17, 2020</div><p>Lorem ipsum dolor sit amet, consectetur adipiscing elit, sed do eiusmod</p><span class="more">READ MORE ⟶</span></article>
  <article class="abs blog" style="left:452px;top:2299px"><h4>Lorem ipsum dolor sit amet</h4><div class="date">Jun 12, 2020</div><p>Lorem ipsum dolor sit amet, consectetur adipiscing elit, sed do eiusmod</p><span class="more">READ MORE ⟶</span></article>
  <article class="abs blog" style="left:790px;top:2299px"><h4>Lorem ipsum dolor sit amet</h4><div class="date">Jun 10, 2020</div><p>Lorem ipsum dolor sit amet, consectetur adipiscing elit, sed do eiusmod</p><span class="more">READ MORE ⟶</span></article>

  <div class="abs btn-purple">VIEW MORE BLOG</div>
</section>

<section>
  <div class="abs contact"></div>
  <h2 class="abs contact-title">Contact us</h2>
  <div class="abs" style="left:554px;top:2782px;width:92px;height:3px;background:var(--white)"></div>
  <div class="abs field" style="left:223px;top:2814px;width:366px">First name</div>
  <div class="abs field" style="left:610px;top:2814px;width:366px">Last name</div>
  <div class="abs field" style="left:223px;top:2890px;width:366px">Email address</div>
  <div class="abs field" style="left:610px;top:2890px;width:366px">Subject</div>
  <div class="abs field" style="left:223px;top:2967px;width:753px">Phone number</div>
  <div class="abs btn-submit">SUBMIT</div>
</section>

<footer>
  <div class="abs footer"></div>
  <div class="abs news-label">Subscribe The Newsletter</div>
  <div class="abs news-input">Email address</div>
  <div class="abs btn-sub">SUBSCRIBE</div>
  <div class="abs footer-nav">
    <span>HOME</span><span>|</span><span>ABOUT</span><span>|</span><span>FEATURES</span><span>|</span><span>PRICES</span><span>|</span><span>BLOG</span><span>|</span><span>REVIEWS</span><span>|</span><span>CONTACT</span>
  </div>
  <div class="abs social" style="left:504px" role="img" aria-label="Social link"></div>
  <div class="abs social" style="left:555px" role="img" aria-label="Social link"></div>
  <div class="abs social" style="left:605px" role="img" aria-label="Social link"></div>
  <div class="abs social" style="left:656px" role="img" aria-label="Social link"></div>
  <div class="abs footer-rule"></div>
  <div class="abs copyright">© Copyrights 2021 Company name | All Rights Reserved</div>
</footer>

</body>
</html>
```